Black Matte card with samurai logo which I would like it to be textured and company name on one side and on the other side I would like the company information with the reno (Face logo) Sushi logo. Double Sided card.

majority customers are University students, University sororities and fraternities.

It Company

Reno Sushi
317 W. Harlow Ave
Tucson, AZ 85042
Phone (520)413-6271
Fax (520)357-1846
E-mail: Renosushidesert@mailbox-example.com
FB: Renosushidesert
Twitter: Renosushidesert

• Present Normal

```html
<!DOCTYPE html>
<html lang="en">
<head>
<meta charset="utf-8">
<title>Reno Sushi – Business Card</title>
<link rel="stylesheet" href="https://fonts.googleapis.com/css2?family=Source+Sans+3:wght@400;600&display=swap">
<style>
  :root {
    --backdrop: #ebe7e1;
    --card-white: #ffffff;
    --ink: #231f20;
    --text-grey: #4d4d4d;
    --brand-red: #b3302a;
    --back-red: #c9373a;
    --mark-dark: #2b2728;
    --divider: #c9c9c9;
    --social-square: #d7dde3;
    --matte-top: #2a2a2a;
    --matte-bottom: #0e0e0e;
  }
  * { margin: 0; padding: 0; box-sizing: border-box; }
  html, body {
    width: 1200px; height: 1183px; overflow: hidden;
    background: var(--backdrop);
    font-family: "Source Sans 3", "Myriad Pro", sans-serif;
  }
  .canvas { position: relative; width: 1200px; height: 1183px; }

  .card { position: absolute; width: 880px; height: 502px; overflow: hidden; }
  .card--front { left: 45px; top: 69px; background: var(--card-white); box-shadow: 0 2px 6px rgba(0,0,0,.25); }
  .card--back {
    left: 260px; top: 614px;
    background: radial-gradient(ellipse at 45% 40%, var(--matte-top), var(--matte-bottom) 80%);
    box-shadow: 0 2px 6px rgba(0,0,0,.3);
  }

  .brand-mark { position: absolute; border-radius: 50%; }
  .brand-mark--front { left: 144px; top: 50px; width: 170px; height: 170px; background: var(--mark-dark); }
  .brand-mark--back { left: 305px; top: 55px; width: 270px; height: 270px; background: #3a3637; }

  .brand-name {
    position: absolute; left: 114px; top: 244px; width: 230px;
    text-align: center; color: var(--brand-red);
    font-size: 50px; font-weight: 400; line-height: 1;
  }
  .divider { position: absolute; left: 385px; top: 83px; width: 1px; height: 196px; background: var(--divider); }

  .contact { position: absolute; left: 413px; top: 98px; list-style: none; color: var(--text-grey); font-size: 21px; }
  .contact li { display: flex; align-items: center; height: 33px; }
  .contact svg { width: 18px; height: 18px; margin-right: 12px; flex: none; }
  .address { position: absolute; left: 413px; top: 215px; color: var(--text-grey); font-size: 21px; line-height: 31px; }

  .wave { position: absolute; left: 0; top: 0; width: 880px; height: 502px; }

  .social { position: absolute; left: 115px; top: 424px; list-style: none; color: #fff; font-size: 21px; }
  .social li { display: flex; align-items: center; height: 32px; }
  .social .square { width: 19px; height: 19px; background: var(--social-square); margin-right: 14px; }

  .back-name {
    position: absolute; left: 0; top: 360px; width: 880px;
    text-align: center; color: var(--back-red);
    font-size: 84px; font-weight: 400; line-height: 1;
  }
</style>
</head>
<body>
<main class="canvas">

  <section class="card card--front" aria-label="Card front">
    <div class="brand-mark brand-mark--front" role="img" aria-label="Reno Sushi brand mark"></div>
    <div class="brand-name">Reno Sushi</div>
    <div class="divider"></div>

    <ul class="contact">
      <li>
        <svg viewBox="0 0 20 20" aria-hidden="true"><circle cx="10" cy="10" r="8.5" fill="none" stroke="var(--brand-red)" stroke-width="2"/><path d="M7 5.5l2 2-1.2 1.5c.7 1.4 1.8 2.5 3.2 3.2l1.5-1.2 2 2-1.5 1.5c-3.5-.6-6.5-3.6-7.1-7.1z" fill="var(--brand-red)"/></svg>
        (520)413-6271
      </li>
      <li>
        <svg viewBox="0 0 20 20" aria-hidden="true"><rect x="5" y="1" width="10" height="18" rx="2" fill="var(--brand-red)"/><rect x="7" y="4" width="6" height="6" fill="#fff"/><rect x="7" y="12" width="6" height="4" fill="#fff" opacity=".6"/></svg>
        (520)357-1846
      </li>
      <li>
        <svg viewBox="0 0 20 20" aria-hidden="true"><rect x="1" y="5" width="18" height="12" rx="1" fill="var(--brand-red)"/><path d="M1.5 6l8.5 6 8.5-6" fill="none" stroke="#fff" stroke-width="1.5"/></svg>
        Renosushidesert@mailbox-example.com
      </li>
    </ul>

    <p class="address">Reno Sushi 317 W. Harlow Ave Tucson<br>AZ 85042</p>

    <svg class="wave" viewBox="0 0 880 502" aria-hidden="true">
      <path class="wave-base" d="M0 422 C220 396 420 436 600 462 C720 478 820 444 880 402 L880 502 L0 502 Z" fill="var(--ink)"/>
      <path class="wave-band" d="M-10 403 C220 372 420 410 600 446 C720 468 820 436 890 380" fill="none" stroke="var(--brand-red)" stroke-width="8"/>
      <path class="wave-gap" d="M450 452 C620 500 770 488 890 438" fill="none" stroke="#fff" stroke-width="14"/>
      <path class="wave-accent" d="M450 452 C620 500 770 488 890 438" fill="none" stroke="var(--brand-red)" stroke-width="7"/>
    </svg>

    <ul class="social">
      <li><span class="square"></span>Renosushidesert</li>
      <li><span class="square"></span>Renosushidesert</li>
    </ul>
  </section>

  <section class="card card--back" role="img" aria-label="Card back: textured matte black surface with the Reno Sushi mark and name">
    <div class="brand-mark brand-mark--back"></div>
    <div class="back-name">Reno Sushi</div>
  </section>

</main>
</body>
</html>
```